Retainer Care Instructions

Please make this PDF - more modern and easy to read for patients. Our demographic is predominately adolescents. All the information is important and text needs to remain relatively the same - can be simplified. Here is a link to care instructions that look nice https://www.brightlane-grins.com/resources

Target Market(s)

Parents and Children

Industry/Entity Type

Orthodontics

Colors
0054AA
0677BA
7BADD7
CADEEF
E8F1F8

Requirements
Must have
• Simple and clear
Nice to have
• Add graphics and images to look more modern
Should not have
• Graphics to demonstrate

```html
<!DOCTYPE html>
<html lang="en">
<head>
<meta charset="utf-8">
<title>Looking After Your Retainers – Northgate Orthodontics</title>
<link rel="stylesheet" href="https://fonts.googleapis.com/css2?family=Plus+Jakarta+Sans:wght@300;400;500;600;700;800&display=swap">
<style>
  :root {
    --board: #8eaed6;
    --paper: #ffffff;
    --ink: #1a1a1a;
    --muted: #3a3a3a;
    --brand-blue: #1597d8;
    --logo-grey: #9a9a9f;
    --panel-grey: #eef1f5;
    --sky: #e3f0f8;
    --tooth: #e9ecef;
  }
  * { box-sizing: border-box; margin: 0; padding: 0; }
  html, body { width: 899px; height: 1200px; overflow: hidden; }
  body {
    background: var(--board);
    font-family: "Plus Jakarta Sans", sans-serif;
    color: var(--ink);
    position: relative;
  }
  .page-label {
    position: absolute;
    width: 384px;
    text-align: center;
    color: #fff;
    font-size: 17px;
    font-weight: 400;
    letter-spacing: 2.5px;
  }
  .page {
    position: absolute;
    width: 384px;
    height: 542px;
    background: var(--paper);
    overflow: hidden;
  }
  .page > * { position: absolute; }
  .art { border-radius: 6px; }
  .tooth {
    width: 38px; height: 52px;
    border-radius: 45% 45% 35% 35%;
    background: radial-gradient(circle at 35% 30%, #ffffff, var(--tooth) 70%, #cfd4d9);
  }
  .blue { color: var(--brand-blue); }

  /* brand name */
  .brand {
    display: flex; align-items: center; gap: 6px;
    font-weight: 700; color: var(--logo-grey);
    white-space: nowrap;
  }
  .brand-dot { width: 12px; height: 12px; border-radius: 50%; background: var(--brand-blue); flex: none; }

  /* title page */
  .cover-brand { left: 72px; top: 48px; font-size: 21px; }
  .cover-hero { left: 8px; top: 141px; width: 372px; height: 236px;
    background: radial-gradient(ellipse at 45% 55%, #2a5fc0 0 22%, #e9edf2 45%, #f6f7f9 75%); }
  .cover-title { left: 0; width: 384px; top: 380px; text-align: center;
    font-weight: 800; font-size: 27px; line-height: 26px; letter-spacing: -0.3px; }
  .cover-rule { left: 98px; top: 441px; width: 187px; height: 1px; background: var(--brand-blue); }
  .cover-sub { left: 0; width: 384px; top: 452px; text-align: center; font-weight: 800; font-size: 16.5px; letter-spacing: -0.2px; }
  .cover-tag { left: 83px; top: 479px; width: 204px; height: 30px; background: var(--brand-blue);
    color: #fff; font-weight: 800; font-size: 16px; line-height: 30px; text-align: center;
    transform: rotate(-2deg); border-radius: 2px; }

  /* page 1 */
  .p1-bg { left: 0; top: 0; width: 384px; height: 542px;
    background: linear-gradient(110deg, #ffffff 45%, var(--sky) 100%); }
  .lead { font-size: 13px; font-weight: 500; line-height: 15.6px; }
  .p1-lead { left: 23px; top: 36px; width: 176px; }
  .p1-lead-blue { left: 23px; top: 90px; width: 180px; font-weight: 600; }
  .p1-retainers { left: 200px; top: 20px; width: 184px; height: 172px;
    background: radial-gradient(ellipse at center, #f4f7f9 30%, rgba(255,255,255,0) 72%); }
  .p1-photo { left: 222px; top: 252px; width: 162px; height: 290px;
    background: linear-gradient(180deg, #d9a07a 0%, #c47a4e 35%, #f2efea 62%, #e8e4de 100%);
    border-radius: 50% 50% 0 0 / 22% 22% 0 0; }
  .notice-box { left: 21px; top: 158px; width: 210px; height: 268px; background: var(--panel-grey); border-radius: 3px; }
  .notice-title { left: 30px; top: 174px; font-size: 16.5px; font-weight: 800; line-height: 18px; letter-spacing: -0.3px; }
  .notice-text { left: 30px; top: 216px; width: 192px; font-size: 12px; font-weight: 300; line-height: 15.6px; color: var(--muted); }
  .notice-caps { left: 30px; top: 370px; width: 195px; font-size: 12px; line-height: 15.6px; }
  .cta { left: 16px; top: 443px; width: 190px; height: 47px; background: var(--brand-blue); border-radius: 3px;
    color: #fff; font-weight: 800; font-size: 14px; line-height: 16px; padding: 7px 0 0 14px; letter-spacing: -0.2px; }

  /* page 2 */
  .p2-lead { left: 23px; top: 27px; width: 200px; }
  .p2-lead-blue { left: 23px; top: 90px; width: 200px; font-weight: 600; }
  .body-copy { font-size: 11px; font-weight: 300; line-height: 14px; color: var(--muted); }
  .p2-research { left: 23px; top: 125px; width: 330px; }
  .info-box { left: 21px; top: 194px; width: 210px; height: 121px; background: var(--brand-blue); border-radius: 3px;
    color: #fff; font-size: 11px; line-height: 13.9px; font-weight: 400; padding: 11px 10px 0 12px; }
  .p2-retainers { left: 239px; top: 206px; width: 130px; height: 96px;
    background: linear-gradient(180deg, #f3f5f7, #e6eaee 50%, #f3f5f7); }
  .warning-box { left: 205px; top: 305px; width: 164px; height: 237px; background: var(--panel-grey); border-radius: 3px 3px 0 0; }
  .warning-title { left: 216px; top: 316px; font-size: 11.5px; font-weight: 800; }
  .warning-text { left: 216px; top: 333px; width: 148px; font-size: 9.6px; line-height: 12.5px; font-weight: 400; color: var(--ink); }
  .warning-text strong { font-weight: 700; }
  .p2-model { left: 188px; top: 455px; width: 124px; height: 87px;
    background: linear-gradient(180deg, #e46a6a 0%, #f1f1f1 45%, #e36a68 100%); border-radius: 10px 10px 0 0; }
  .cleaning-title { left: 21px; top: 335px; font-size: 19px; font-weight: 800; line-height: 18px; letter-spacing: -0.3px; }
  .cleaning-text { left: 23px; top: 376px; width: 176px; font-size: 10.6px; line-height: 13.6px; font-weight: 400; color: var(--ink); }

  /* last page */
  .back-photo { left: 0; top: 0; width: 384px; height: 331px;
    background: linear-gradient(180deg, #cfd6dc 0%, #a9c9dc 45%, #d7c7c0 65%, #ffffff 100%); }
  .back-brand { left: 33px; top: 380px; font-size: 19px; }
  .contact { display: flex; align-items: flex-start; gap: 7px; }
  .contact svg { flex: none; }
  .phone { left: 30px; top: 416px; font-size: 19.5px; font-weight: 700; }
  .address { left: 34px; top: 455px; font-size: 11px; line-height: 13.5px; font-weight: 300; color: var(--muted); }
  .email { left: 34px; top: 500px; font-size: 11px; font-weight: 300; color: var(--muted); }
</style>
</head>
<body>

  <div class="page-label" style="left:60px; top:22px;">TITLE PAGE</div>
  <div class="page-label" style="left:455px; top:22px;">PAGE 1</div>
  <div class="page-label" style="left:60px; top:1157px;">PAGE 2</div>
  <div class="page-label" style="left:455px; top:1157px;">LAST PAGE</div>

  <!-- Title page -->
  <section class="page cover" style="left:60px; top:52px;">
    <div class="brand cover-brand"><span class="brand-dot"></span>northgate orthodontics</div>
    <div class="cover-hero art" role="img" aria-label="Clear retainer resting on a blue retainer case beside a tooth mascot in a lab coat"></div>
    <div class="tooth" role="img" aria-label="White tooth illustration" style="left:48px; top:86px; transform:rotate(-10deg);"></div>
    <div class="tooth" role="img" aria-label="White tooth illustration" style="left:316px; top:458px; transform:rotate(20deg);"></div>
    <h1 class="cover-title">LOOKING AFTER<br>YOUR <span class="blue">RETAINERS</span></h1>
    <div class="cover-rule"></div>
    <p class="cover-sub">THE BRACES ARE OFF<span class="blue">...</span></p>
    <p class="cover-tag">IT'S RETAINER TIME!</p>
  </section>

  <!-- Page 1 -->
  <section class="page" style="left:455px; top:52px;">
    <div class="p1-bg"></div>
    <div class="p1-retainers art" role="img" aria-label="Pair of clear retainers"></div>
    <p class="lead p1-lead">Always wear your retainer as instructed by your orthodontist.</p>
    <p class="lead p1-lead-blue blue">Remember to take your retainer out when eating &amp; playing sport.</p>
    <div class="p1-photo" role="img" aria-label="Smiling young woman pointing at her straight teeth"></div>
    <div class="notice-box"></div>
    <h2 class="notice-title">DO NOT LOSE<br>YOUR RETAINER!!!</h2>
    <p class="notice-text">The cost of your first retainers is covered in the fee for your treatment. However, if they are lost or broken and need replacement, this will incur an additional fee of $300 for a new one and we will have to take a new impression, So please look after it.</p>
    <p class="notice-caps blue">ALWAYS STORE IN THE RETAINER CONTAINER PROVIDED</p>
    <div class="tooth" role="img" aria-label="White tooth illustration" style="left:215px; top:222px; transform:rotate(12deg);"></div>
    <p class="cta">SO DON'T FORGET<br>YOUR RETAINER!!!</p>
    <div class="tooth" role="img" aria-label="White tooth illustration" style="left:186px; top:478px; transform:rotate(-15deg);"></div>
  </section>

  <!-- Page 2 -->
  <section class="page" style="left:60px; top:606px;">
    <p class="lead p2-lead">If you want to keep your teeth straight never throw your retainers away!</p>
    <p class="lead p2-lead-blue blue">It's up to you from here on...<br>Why is this needed?</p>
    <div class="tooth" role="img" aria-label="White tooth illustration" style="left:240px; top:20px; transform:rotate(-8deg);"></div>
    <div class="tooth" role="img" aria-label="White tooth illustration" style="left:296px; top:46px; transform:rotate(18deg);"></div>
    <p class="body-copy p2-research">Long-term clinical research shows that no matter how well teeth are straightened, they will show a tendency for some movement over many years (probably throughout life). By the way, this also occurs with teeth that haven't had any orthodontic treatment.</p>
    <div class="info-box">This tooth movement often shows up as an increase in crowding of the front teeth, by trying your retainers in every so often and if necessary wearing them occasionally you can keep your teeth straight for the years ahead.</div>
    <div class="p2-retainers art" role="img" aria-label="Upper and lower clear retainers"></div>
    <div class="warning-box"></div>
    <h3 class="warning-title">WARNING</h3>
    <p class="warning-text"><strong>DO NOT PLACE TABLETS IN MOUTH.</strong> Do not use to clean natural teeth, Keep product out of reach of children. In case of accidental ingestion seek professional assistance or contact poison centre immediately <strong>13-55-010</strong></p>
    <div class="p2-model art" role="img" aria-label="Dental model of teeth with braces"></div>
    <h2 class="cleaning-title blue">CLEANING<br>TABLETS</h2>
    <p class="cleaning-text">Drop one tablet into enough warm (Not Hot) water to cover the appliance place appliance into the bubbling solution Leave for 10-15 mins and appliance is clean and odor free rinse thoroughly with running water.</p>
  </section>

  <!-- Last page -->
  <section class="page" style="left:455px; top:606px;">
    <div class="back-photo" role="img" aria-label="Patient in a dental chair being examined by an orthodontist"></div>
    <div class="tooth" role="img" aria-label="White tooth illustration" style="left:228px; top:318px; width:48px; height:66px; transform:rotate(-10deg);"></div>
    <div class="tooth" role="img" aria-label="White tooth illustration" style="left:290px; top:438px; transform:rotate(14deg);"></div>
    <div class="brand back-brand"><span class="brand-dot"></span>northgate orthodontics</div>
    <div class="contact phone">
      <svg width="18" height="18" viewBox="0 0 24 24" aria-hidden="true"><path fill="#1597d8" d="M6.6 10.8a15.1 15.1 0 0 0 6.6 6.6l2.2-2.2a1 1 0 0 1 1-.25 11.4 11.4 0 0 0 3.6.57 1 1 0 0 1 1 1V20a1 1 0 0 1-1 1A17 17 0 0 1 3 4a1 1 0 0 1 1-1h3.5a1 1 0 0 1 1 1c0 1.25.2 2.450.57 3.57a1 1 0 0 1-.25 1z"/></svg>
      <span>9555 0142</span>
    </div>
    <div class="contact address">
      <svg width="11" height="13" viewBox="0 0 24 28" aria-hidden="true"><path fill="#1597d8" d="M12 0a9 9 0 0 0-9 9c0 7 9 17 9 17s9-10 9-17a9 9 0 0 0-9-9zm0 12.5A3.5 3.5 0 1 1 12 5.5a3.5 3.5 0 0 1 0 7z"/></svg>
      <span>48 Lindell Road<br>ASHVALE VIC 3199</span>
    </div>
    <div class="contact email">
      <svg width="11" height="9" viewBox="0 0 24 18" aria-hidden="true"><path fill="#1597d8" d="M0 0h24v2L12 10 0 2zM0 4.5l12 8 12-8V18H0z"/></svg>
      <span>hello@northgate-ortho.com.au</span>
    </div>
  </section>

</body>
</html>
```